New travel store signage for Marlow Journeys to attract luxury travellers.

Hello,
We are looking to change the signage of our stores. The signage must include the following:
1. Marlow Journeys Logo (attached)
2. The text...The Travel & Cruise Experts
3. Brand Colours ( Fb0196, 412266, d41d84 and ffffff)
Please note the signage design must be central and only cover two thirds of the store front. We have also attached an image of one of our new stores which might be helpful when preparing a mock up.

We are looking for a quick turnaround on this, making a decision within 48 hours.

Target Market(s)

Retail

Industry/Entity Type

Travel Agency

Font styles to use
Other font styles liked:
• Radley

Colors
E54698
E96AAD
F1A4CE
F9D9EA
FCEFF6
6B429C
8869AF
B7A5CE
E3DAEB
F3F0F8

Requirements
Must have
• Hello, We are looking to change the signage of our stores. The signage must include the following: 1. Marlow Journeys Logo (attached) 2. The text...The Travel & Cruise Experts 3. Brand Colours ( Fb0196, 412266, d41d84 and ffffff) Please note the signage design must be central and only cover two thirds of the store front.
Should not have
• different colour or fonts. Gradient design.

```html
<!DOCTYPE html>
<html lang="en">
<head>
<meta charset="utf-8">
<title>Marlow Journeys – Store Signage</title>
<link href="https://fonts.googleapis.com/css2?family=Radley&display=swap" rel="stylesheet">
<style>
  :root {
    --brand-deep: #412266;
    --brand-magenta: #d41d84;
    --band-dark: #4b1f6f;
    --band-light: #84177a;
    --white: #ffffff;
    --backdrop: #ffffff;
  }
  * { margin: 0; padding: 0; box-sizing: border-box; }
  html, body {
    width: 1200px;
    height: 1199px;
    overflow: hidden;
    background: var(--backdrop);
  }
  .canvas {
    position: relative;
    width: 1200px;
    height: 1199px;
  }
  .shop-sign {
    position: absolute;
    left: 32px;
    top: 518px;
    width: 1138px;
    height: 162px;
  }
  .sign-art {
    position: absolute;
    inset: 0;
    width: 100%;
    height: 100%;
    display: block;
  }
  .brand-name {
    position: absolute;
    left: 392px;
    top: 90px;
    display: flex;
    align-items: center;
    gap: 10px;
    font-family: "Radley", serif;
    font-size: 25px;
    line-height: 1;
    color: var(--brand-deep);
    white-space: nowrap;
  }
  .brand-dot {
    width: 12px;
    height: 12px;
    border-radius: 50%;
    background: var(--brand-magenta);
  }
  .tagline {
    position: absolute;
    left: 662px;
    top: 68px;
    font-family: "Radley", serif;
    font-size: 22px;
    line-height: 23px;
    color: var(--brand-deep);
    white-space: nowrap;
  }
</style>
</head>
<body>
  <main class="canvas">
    <section class="shop-sign" aria-label="Marlow Journeys store sign">
      <svg class="sign-art" viewBox="0 0 1422 202" preserveAspectRatio="none" aria-hidden="true">
        <defs>
          <linearGradient id="bandGradient" x1="0" y1="1" x2="1" y2="0">
            <stop offset="0" stop-color="#4b1f6f"/>
            <stop offset="1" stop-color="#84177a"/>
          </linearGradient>
        </defs>
        <rect class="band" x="0" y="0" width="1422" height="202" fill="url(#bandGradient)"/>
        <path class="panel" fill="#ffffff"
          d="M465,0 L1100,0 C1170,50 1150,150 1050,202 L343,202 C300,130 360,55 465,0 Z"/>
      </svg>

      <div class="brand-name">
        <span class="brand-dot" aria-hidden="true"></span>
        <span>Marlow Journeys</span>
      </div>

      <p class="tagline">The Travel<br>&amp; Cruise Experts</p>
    </section>
  </main>
</body>
</html>
```